Business Card Design - Amberfield Court

We are looking at a new design for our business cards that has a modern and professional look. We run a residential aged care facility focussing on the care of residents. The cards will be used for potential clients, consultants and business opportunities in this sector. Blue and white is our main colours and would to see these colours incorporated in the design.
Industry/Entity Type
Business
Contact Information for Business Card
Amberfield Court, Darren Walsh, dwalsh@amberfieldcourt.com.au, Finance Manager, 0472 639 208, BCom, 37 Marrabel Crescent, Brindle Vale, Qld 4093.
Look and feel
Each slider illustrates characteristics of the customer's brand and the style your logo design should communicate.

```html
<!DOCTYPE html>
<html lang="en">
<head>
<meta charset="utf-8">
<title>Amberfield Court – Business Card</title>
<link href="https://fonts.googleapis.com/css2?family=Open+Sans:wght@400;600;700&display=swap" rel="stylesheet">
<style>
  :root {
    --navy: #1d3d4f;
    --steel: #5b8298;
    --taupe: #aea399;
    --taupe-deep: #9c9187;
    --white: #ffffff;
    --ink: #3e3a37;
    --page: #e9e7e4;
  }
  * { box-sizing: border-box; margin: 0; padding: 0; }
  html, body {
    width: 1200px; height: 900px; overflow: hidden;
    background: var(--page);
    font-family: "Open Sans", Arial, sans-serif;
  }
  .canvas { position: relative; width: 1200px; height: 900px; }

  .card {
    position: absolute;
    width: 640px; height: 366px;
    border-radius: 26px;
    overflow: hidden;
    box-shadow: 0 10px 30px rgba(0,0,0,0.18);
  }

  /* Front */
  .card-front { left: 110px; top: 60px; background: var(--white); }
  .front-wordmark {
    position: absolute; inset: 0;
    display: flex; align-items: center; justify-content: center; gap: 16px;
  }
  .brand-dot { width: 26px; height: 26px; border-radius: 50%; background: var(--navy); }
  .brand-name {
    font-weight: 700; font-size: 38px; letter-spacing: 3px;
    color: var(--navy); text-transform: uppercase;
  }

  /* Back */
  .card-back { left: 450px; top: 474px; background: var(--taupe); }
  .back-band {
    position: absolute; left: 0; right: 0; top: 112px; height: 150px;
    background: var(--white);
  }
  .faint-name {
    position: absolute; left: 40px; top: 66px;
    font-weight: 700; font-size: 34px; letter-spacing: 3px;
    color: var(--taupe-deep); opacity: 0.55; text-transform: uppercase;
  }
  .back-brand {
    position: absolute; right: 34px; top: 140px;
    display: flex; align-items: center; gap: 10px;
  }
  .back-brand .brand-dot { width: 16px; height: 16px; }
  .back-brand .brand-name { font-size: 20px; letter-spacing: 1.5px; }

  .holder {
    position: absolute; left: 34px; top: 196px;
    display: flex; align-items: center; gap: 14px;
  }
  .holder-marks { display: flex; gap: 4px; }
  .holder-marks span { display: block; width: 14px; height: 30px; }
  .holder-marks span:first-child { background: var(--navy); width: 22px; }
  .holder-marks span:last-child { background: var(--steel); }
  .holder-name { font-weight: 700; font-size: 27px; line-height: 1; color: var(--navy); text-transform: uppercase; }
  .holder-role { font-size: 13px; color: var(--navy); text-transform: uppercase; letter-spacing: 0.3px; margin-top: 3px; }

  .contact {
    position: absolute; left: 40px; top: 282px;
    list-style: none; color: var(--ink); font-size: 16px; line-height: 1.45;
  }
  .contact li { display: flex; align-items: center; gap: 8px; }
  .contact svg { width: 13px; height: 13px; fill: var(--ink); }

  .address {
    position: absolute; right: 34px; top: 196px;
    text-align: right; color: var(--ink); font-size: 16px; line-height: 1.4;
    font-style: normal;
  }
  .card-back .address { top: 272px; }
</style>
</head>
<body>
<main class="canvas">
  <section class="card card-front" aria-label="Card front">
    <div class="front-wordmark">
      <span class="brand-dot"></span>
      <span class="brand-name">Amberfield Court</span>
    </div>
  </section>

  <section class="card card-back" aria-label="Card back">
    <div class="faint-name" aria-hidden="true">Amberfield Court</div>
    <div class="back-band"></div>

    <div class="back-brand">
      <span class="brand-dot"></span>
      <span class="brand-name">Amberfield Court</span>
    </div>

    <div class="holder">
      <div class="holder-marks"><span></span><span></span></div>
      <div>
        <p class="holder-name">Darren Walsh</p>
        <p class="holder-role">Finance Manager (BCom)</p>
      </div>
    </div>

    <ul class="contact">
      <li>
        <svg viewBox="0 0 24 24" aria-hidden="true"><path d="M6.6 10.8a15 15 0 0 0 6.6 6.6l2.2-2.2c.3-.3.7-.4 1-.2 1.1.4 2.3.6 3.6.6.6 0 1 .4 1 1V20c0 .6-.4 1-1 1A17 17 0 0 1 3 4c0-.6.4-1 1-1h3.5c.6 0 1 .4 1 1 0 1.3.2 2.5.6 3.6.1.3 0 .7-.2 1l-2.3 2.2z"/></svg>
        0472 639 208
      </li>
      <li>
        <svg viewBox="0 0 24 24" aria-hidden="true"><path d="M2 5h20v14H2V5zm2 2v.5l8 5 8-5V7H4zm16 2.8-8 5-8-5V17h16V9.8z"/></svg>
        dwalsh@amberfieldcourt.com.au
      </li>
    </ul>

    <address class="address">
      37 Marrabel Crescent<br>
      Brindle Vale, Qld 4093
    </address>
  </section>
</main>
</body>
</html>
```